KRWB new business card design

We need a business card design for our established business which is Australia wide however based in Melbourne. We are a young team of Financial Planners who specialize in Insurance and Basic super advice for people like us.

We are people who help our clients get things done in a timely and cost effective manner whilst having a good time and a laugh along the way.

We would like this to have a consistent feel with our new e-brochure which i have attached from a color and font perspective.

Industry/Entity Type

Business

Requirements
Must have
• We do not need specific address details rather just the states we are in:

VIC/NSW/QLD/TAS
Nice to have
• Curved edge to mate the brochure

```html
<!DOCTYPE html>
<html lang="en">
<head>
<meta charset="utf-8">
<title>KRWB business card concepts</title>
<link rel="stylesheet" href="https://fonts.googleapis.com/css2?family=Cabin:wght@400;600;700&family=Arimo:wght@400;700&display=swap">
<style>
  :root {
    --bg: #d8d3cb;
    --card: #000000;
    --white: #ffffff;
    --green-dark: #1f9e46;
    --green-light: #8cc63f;
    --edge: #6cbf3f;
    --photo-top: #6a6a6a;
    --photo-bottom: #cfcfcf;
  }
  * { margin: 0; padding: 0; box-sizing: border-box; }
  html, body { width: 1200px; height: 502px; overflow: hidden; background: var(--bg); }
  body { position: relative; font-family: "Cabin", sans-serif; color: var(--white); }

  .card {
    position: absolute;
    width: 354px;
    height: 204px;
    background: var(--card);
    border-bottom-right-radius: 34px;
    overflow: hidden;
  }
  .card--edged { border-right: 4px solid var(--edge); }

  .card--contact  { left: 39px;  top: 26px; }
  .card--portrait { left: 425px; top: 28px; }
  .card--columns  { left: 815px; top: 31px; }
  .card--web      { left: 38px;  top: 274px; }
  .card--split    { left: 432px; top: 273px; }
  .card--list     { left: 818px; top: 278px; }

  .brand {
    display: flex;
    align-items: center;
    justify-content: center;
    gap: 8px;
    font-family: "Cabin", sans-serif;
    font-weight: 700;
    color: var(--green-light);
    letter-spacing: 2px;
  }
  .brand__square { display: block; background: var(--green-dark); }
  .brand--white { color: var(--white); }
  .brand--white .brand__square { background: var(--white); }

  .heading {
    font-weight: 700;
    font-size: 13px;
    letter-spacing: 2.6px;
    text-align: center;
  }
  .services { list-style: none; font-size: 13px; line-height: 1.45; }
  .services li::before { content: "\2022"; margin-right: 5px; }
  .services-inline { text-align: center; font-size: 13px; line-height: 1.55; }
  .services-inline span::before { content: "\2022 "; }
  .services-inline .services-inline__green::before { color: var(--green-light); }

  /* card 1 */
  .contact__head { position: absolute; left: 0; top: 8px; width: 300px; text-align: center; font-family: "Arimo", sans-serif; }
  .contact__name { font-size: 13px; font-weight: 700; }
  .contact__name em { font-weight: 400; font-size: 11px; }
  .contact__role { font-size: 12px; margin-top: 1px; }
  .contact__legal { font-size: 7.5px; line-height: 1.2; margin-top: 3px; }
  .card--contact .brand { position: absolute; left: 125px; top: 100px; width: 70px; font-size: 17px; }
  .card--contact .brand__square { width: 12px; height: 12px; }
  .contact__details { position: absolute; left: 0; top: 168px; width: 330px; text-align: center; font-family: "Arimo", sans-serif; font-size: 9.5px; line-height: 1.6; }
  .contact__details svg { width: 8px; height: 8px; vertical-align: -1px; margin-right: 2px; fill: var(--white); }
  .contact__details .gap { margin-left: 8px; }

  /* card 2 */
  .portrait__photo { position: absolute; right: 0; top: 0; width: 54px; height: 204px; background: linear-gradient(180deg, var(--photo-top), var(--photo-bottom) 55%, var(--photo-top)); }
  .card--portrait .brand { position: absolute; left: 80px; top: 40px; width: 130px; font-size: 30px; }
  .card--portrait .brand__square { width: 20px; height: 20px; }
  .card--portrait .heading { position: absolute; left: 0; top: 127px; width: 296px; }
  .card--portrait .services-inline { position: absolute; left: 0; top: 145px; width: 296px; font-size: 12.5px; }

  /* card 3 */
  .card--columns .brand { position: absolute; left: 0; top: 45px; width: 100%; font-size: 32px; }
  .card--columns .brand__square { width: 22px; height: 22px; }
  .card--columns .heading { position: absolute; left: 0; top: 144px; width: 100%; }
  .columns { position: absolute; left: 14px; top: 165px; display: flex; font-size: 11px; line-height: 1.35; }
  .columns ul { list-style: none; padding: 0 8px; }
  .columns ul + ul { border-left: 1px solid var(--green-light); }
  .columns li::before { content: "\2022 "; color: var(--green-light); }
  .columns .columns__low { padding-top: 14px; }

  /* card 4 */
  .card--web .brand { position: absolute; left: 0; top: 30px; width: 100%; font-size: 32px; }
  .card--web .brand__square { width: 22px; height: 22px; }
  .card--web .heading { position: absolute; left: 0; top: 128px; width: 100%; }
  .card--web .services-inline { position: absolute; left: 0; top: 146px; width: 100%; }
  .web__url { position: absolute; left: 0; top: 186px; width: 100%; text-align: center; font-size: 12px; letter-spacing: 3px; }

  /* card 5 */
  .card--split .brand { position: absolute; left: 14px; top: 84px; width: 150px; font-size: 28px; }
  .card--split .brand__square { width: 18px; height: 18px; }
  .split__rule { position: absolute; left: 174px; top: 42px; width: 1px; height: 80px; background: linear-gradient(180deg, transparent, var(--white), transparent); }
  .card--split .heading { position: absolute; left: 188px; top: 44px; text-align: left; }
  .card--split .services { position: absolute; left: 188px; top: 68px; }
  .card--split .services li::before, .card--list .services li::before { color: var(--green-light); }

  /* card 6 */
  .card--list .heading { position: absolute; left: 26px; top: 24px; font-size: 15px; letter-spacing: 3px; text-align: left; }
  .card--list .services { position: absolute; left: 26px; top: 54px; font-size: 16px; line-height: 1.6; }
  .card--list .brand { position: absolute; left: 222px; top: 86px; width: 120px; font-size: 28px; }
  .card--list .brand__square { width: 18px; height: 18px; }
</style>
</head>
<body>

  <section class="card card--contact card--edged">
    <div class="contact__head">
      <p class="contact__name">Daniel Harrow <em>ADFS, BBus, LRS</em></p>
      <p class="contact__role">Financial Adviser</p>
      <p class="contact__legal">KRWB Planning Pty Ltd<br>Authorised Representatives, Corvane Advisory Group Limited<br>Australian Financial Services Licensee</p>
    </div>
    <div class="brand"><span class="brand__square"></span>KRWB</div>
    <div class="contact__details">
      <p>
        <svg viewBox="0 0 10 10"><path d="M2 0h2l1 3-1.5 1a6 6 0 0 0 2.5 2.5L7 5l3 1v2c0 1-1 2-2 2C4 10 0 6 0 2 0 1 1 0 2 0z"/></svg>1300 555 214
        <span class="gap"><svg viewBox="0 0 10 10"><rect x="2.5" y="0" width="5" height="10" rx="1"/></svg>0400 555 781</span>
        <span class="gap"><svg viewBox="0 0 10 10"><path d="M2 0h6v3H2zM0 3h10v5H0zM2 7h6v3H2z"/></svg>03 9555 0147</span>
      </p>
      <p>
        <svg viewBox="0 0 10 10"><path d="M0 2h10v6H0z M0 2l5 4 5-4" fill="none" stroke="#fff" stroke-width="1.2"/></svg>daniel@krwb.com.au
        <span class="gap">States: VIC/NSW/QLD/TAS</span>
      </p>
    </div>
  </section>

  <section class="card card--portrait card--edged">
    <div class="portrait__photo" role="img" aria-label="Black and white portrait photo of a smiling team member"></div>
    <div class="brand"><span class="brand__square"></span>KRWB</div>
    <p class="heading">Specialising in:</p>
    <p class="services-inline">
      <span class="services-inline__green">Risk Insurance</span> <span class="services-inline__green">Debt Management</span><br>
      <span class="services-inline__green">Superannuation</span><br>
      <span class="services-inline__green">Wealth Creation</span> <span class="services-inline__green">Retirement Planning</span>
    </p>
  </section>

  <section class="card card--columns">
    <div class="brand"><span class="brand__square"></span>KRWB</div>
    <p class="heading">Specialising in:</p>
    <div class="columns">
      <ul><li>Risk Insurance</li><li>Debt Management</li></ul>
      <ul><li>Superannuation</li><li>Wealth Creation</li></ul>
      <ul class="columns__low"><li>Retirement Planning</li></ul>
    </div>
  </section>

  <section class="card card--web">
    <div class="brand brand--white"><span class="brand__square"></span>KRWB</div>
    <p class="heading">Specialising in:</p>
    <p class="services-inline">
      <span>Risk Insurance</span> <span>Debt Management</span> <span>Superannuation</span><br>
      <span>Wealth Creation</span> <span>Retirement Planning</span>
    </p>
    <p class="web__url">www.krwb.com.au</p>
  </section>

  <section class="card card--split card--edged">
    <div class="brand"><span class="brand__square"></span>KRWB</div>
    <div class="split__rule"></div>
    <p class="heading">Specialising in:</p>
    <ul class="services">
      <li>Risk Insurance</li>
      <li>Debt Management</li>
      <li>Superannuation</li>
      <li>Wealth Creation</li>
      <li>Retirement Planning</li>
    </ul>
  </section>

  <section class="card card--list">
    <p class="heading">Specialising in:</p>
    <ul class="services">
      <li>Risk Insurance</li>
      <li>Debt Management</li>
      <li>Superannuation</li>
      <li>Wealth Creation</li>
      <li>Retirement Planning</li>
    </ul>
    <div class="brand"><span class="brand__square"></span>KRWB</div>
  </section>

</body>
</html>
```